IT Company looking to market towards Dental Offices

I am looking for a full-color design. Using my existing logo. Must have High Res stock photos. The brochure needs to be full page edge to edge design single fold pamphlet style. Content provided. Please see the website in attached Word Doc for more content.

```html
<!DOCTYPE html>
<html lang="en">
<head>
<meta charset="utf-8">
<title>Byte Harbor – Dental IT Brochure</title>
<link rel="stylesheet" href="https://fonts.googleapis.com/css2?family=Open+Sans:wght@300;400;600;700;800&display=swap">
<style>
  :root {
    --navy: #1a2767;
    --navy-deep: #121c52;
    --blue: #1d6fc8;
    --sky: #3d95e6;
    --ice: #dce9f5;
    --paper: #ffffff;
    --ink: #5a5f6b;
    --stage: #3a3a3a;
  }
  * { box-sizing: border-box; margin: 0; padding: 0; }
  html, body { width: 880px; height: 1200px; overflow: hidden; background: var(--stage); font-family: "Open Sans", Arial, sans-serif; }
  .canvas { position: relative; width: 880px; height: 1200px; }
  .spread { position: absolute; left: 40px; width: 800px; height: 566px; background: var(--paper); overflow: hidden; }
  .spread--outside { top: 22px; }
  .spread--inside { top: 612px; }
  .spread svg.shapes { position: absolute; inset: 0; }
  .abs { position: absolute; }

  /* outside */
  .intro-text { left: 24px; top: 318px; width: 352px; color: var(--paper); font-size: 10.5px; line-height: 1.55; }
  .cta-text { left: 24px; top: 470px; width: 352px; color: var(--ink); font-size: 10.5px; line-height: 1.5; font-weight: 300; }
  .cta-text strong { color: var(--navy); font-weight: 700; }
  .brand { left: 470px; top: 40px; display: flex; align-items: center; gap: 10px; }
  .brand__dot { width: 34px; height: 34px; border-radius: 50%; background: var(--navy); }
  .brand__name { font-size: 26px; font-weight: 700; color: var(--navy); letter-spacing: -0.3px; }
  .badge { left: 670px; top: 300px; width: 130px; text-align: center; color: var(--paper); line-height: 1.1; }
  .badge__small { font-size: 10px; font-weight: 300; }
  .badge__big { font-size: 24px; font-weight: 800; letter-spacing: 0.5px; }
  .badge__mid { font-size: 14px; font-weight: 800; }
  .web { right: 24px; top: 520px; font-size: 11px; color: var(--navy); display: flex; align-items: center; gap: 6px; }
  .web strong { font-weight: 700; }
  .web__dot { width: 10px; height: 10px; border-radius: 50%; background: var(--blue); }

  /* inside */
  .section-title { font-size: 19px; letter-spacing: 0.5px; color: var(--paper); font-weight: 300; }
  .section-title b { font-weight: 800; }
  .rule { display: block; width: 26px; height: 3px; background: var(--paper); margin-top: 4px; }
  .about { left: 30px; top: 28px; width: 310px; }
  .about p { color: var(--paper); font-size: 8.8px; line-height: 1.5; margin-top: 10px; opacity: 0.92; }
  .services { left: 30px; top: 200px; width: 340px; }
  .services__cols { display: flex; gap: 30px; margin-top: 12px; }
  .ticks { list-style: none; color: var(--paper); font-size: 9px; line-height: 1.55; }
  .ticks li::before { content: "\2713"; margin-right: 5px; }
  .ticks li.head { font-weight: 800; text-transform: uppercase; font-size: 8.5px; }
  .solutions { left: 436px; top: 30px; width: 340px; }
  .solutions .section-title { color: var(--navy); }
  .solutions .rule { background: var(--blue); }
  .solutions .ticks { color: #444a57; margin-top: 10px; }
  .solutions .ticks li::before { color: var(--blue); }
  .ready { left: 436px; top: 292px; width: 340px; color: var(--paper); }
  .ready h2 { font-size: 21px; font-weight: 800; line-height: 1.15; letter-spacing: 0.4px; }
  .ready .rule { margin-top: 6px; }
  .ready h3 { font-size: 9.5px; font-weight: 700; margin-top: 12px; }
  .ready .ticks { margin-top: 6px; }
  .ready p { font-size: 9.5px; line-height: 1.5; margin-top: 10px; }
</style>
</head>
<body>
<main class="canvas">

  <!-- Outside spread: back cover + front cover -->
  <section class="spread spread--outside">
    <svg class="shapes" width="800" height="566" viewBox="0 0 800 566">
      <defs>
        <linearGradient id="clinicTone" x1="0" y1="0" x2="1" y2="1">
          <stop offset="0" stop-color="#b9d3ec"/>
          <stop offset="0.5" stop-color="#e8f1fa"/>
          <stop offset="1" stop-color="#8fb7dc"/>
        </linearGradient>
        <radialGradient id="vaultTone" cx="0.45" cy="0.5" r="0.6">
          <stop offset="0" stop-color="#d7d9dc"/>
          <stop offset="0.6" stop-color="#a7abaf"/>
          <stop offset="1" stop-color="#6f6d69"/>
        </radialGradient>
        <clipPath id="coverClip"><rect x="400" y="0" width="400" height="566"/></clipPath>
      </defs>
      <rect class="photo-clinic" x="0" y="0" width="400" height="310" fill="url(#clinicTone)" role="img" aria-label="Photo of a bright modern dental treatment room with a patient chair"/>
      <rect class="band" x="0" y="300" width="400" height="140" fill="var(--blue)"/>
      <g clip-path="url(#coverClip)">
        <path d="M800 0 L800 24 Q740 4 690 0 Z" fill="var(--blue)"/>
        <circle cx="610" cy="290" r="192" fill="none" stroke="var(--navy)" stroke-width="16" stroke-dasharray="560 700" transform="rotate(-60 610 290)"/>
        <circle cx="610" cy="290" r="180" fill="url(#vaultTone)" role="img" aria-label="Photo of a steel bank vault door set in stone"/>
        <circle cx="735" cy="352" r="72" fill="var(--paper)"/>
        <circle cx="735" cy="352" r="66" fill="var(--blue)"/>
      </g>
    </svg>

    <p class="abs intro-text">Byte Harbor offers proven expertise in Dental Practices. We have trained engineers that specialize in Dental practices. We can handle supporting your Practice Management Software to installing IOCs, Remote &amp; Sensors, Pano's, X-rays, scanners, and pen pads. Being familiar with the Digital side of how your practice runs we will be able to predict and plan for your growth by providing the correct configurations and storage needs you will require. We know Dental!</p>
    <p class="abs cta-text">Get started today at <strong>www.chairsidevault.com</strong><br>We don't charge anything until we have confirmation that your Data has been successfully backed up on our encrypted servers.</p>

    <div class="abs brand"><span class="brand__dot"></span><span class="brand__name">Byte Harbor</span></div>
    <div class="abs badge">
      <div class="badge__small">Byte Harbor</div>
      <div class="badge__big">OFFERS</div>
      <div class="badge__small">proven expertise in</div>
      <div class="badge__mid">DENTAL<br>PRACTICES</div>
    </div>
    <div class="abs web"><span class="web__dot"></span><span>www.<strong>maplebytes</strong>.com</span></div>
  </section>

  <!-- Inside spread -->
  <section class="spread spread--inside">
    <svg class="shapes" width="800" height="566" viewBox="0 0 800 566">
      <defs>
        <linearGradient id="navyFade" x1="0" y1="0" x2="1" y2="1">
          <stop offset="0" stop-color="var(--navy-deep)"/>
          <stop offset="1" stop-color="#2b3a86"/>
        </linearGradient>
        <linearGradient id="officeTone" x1="0" y1="0" x2="1" y2="1">
          <stop offset="0" stop-color="#d9dde2"/>
          <stop offset="1" stop-color="#7c8087"/>
        </linearGradient>
        <linearGradient id="serverTone" x1="0" y1="0" x2="1" y2="0">
          <stop offset="0" stop-color="#1a2767" stop-opacity="0"/>
          <stop offset="0.5" stop-color="#2a2d35"/>
          <stop offset="1" stop-color="#15171c"/>
        </linearGradient>
      </defs>
      <rect x="0" y="0" width="400" height="566" fill="url(#navyFade)"/>
      <path d="M300 0 Q390 60 400 190 L400 0 Z" fill="var(--sky)"/>
      <path d="M340 0 Q395 40 400 110 L400 0 Z" fill="var(--blue)"/>
      <path class="photo-office" d="M0 430 L400 380 L400 566 L0 566 Z" fill="url(#officeTone)" role="img" aria-label="Photo of a dental operatory with patient chair and window"/>
      <path d="M400 300 L800 200 L800 566 L400 566 Z" fill="var(--navy)"/>
      <path class="photo-servers" d="M560 260 L800 200 L800 430 Q720 330 560 260 Z" fill="url(#serverTone)" role="img" aria-label="Photo of server racks in a data centre"/>
      <path d="M400 518 Q470 548 580 566 L400 566 Z" fill="var(--sky)"/>
      <path d="M400 540 Q450 558 510 566 L400 566 Z" fill="var(--blue)"/>
    </svg>

    <div class="abs about">
      <h2 class="section-title">ABOUT <b>US</b></h2><span class="rule"></span>
      <p>Byte Harbor offers a proven expertise in Dental Practices. We have trained engineers that specialize in Dental practice management solutions. We can handle supporting your Practice Management Software to installing IOCs, Remote &amp; Sensors, Pano's, X-rays, scanners, pen pads, and more. Being familiar with Digital technology and how your practice runs we are able to predict and plan for your growth by providing the correct configurations the first time and implementing the proper storage solutions you will require. We know Dental!</p>
    </div>

    <div class="abs services">
      <h2 class="section-title">OUR <b>SERVICES</b></h2><span class="rule"></span>
      <div class="services__cols">
        <ul class="ticks">
          <li class="head">Hardware Sales</li>
          <li>Servers</li><li>Workstations</li><li>Firewalls</li><li>Routers</li><li>Switches</li>
          <li>TVs &amp; Monitors</li><li>Wireless Equipment</li><li>Custom Check-in Workstations</li>
        </ul>
        <ul class="ticks">
          <li class="head">Infrastructure</li>
          <li>Data &amp; Voice Cable</li><li>HDMI &amp; COAX Video Cable</li><li>TV &amp; Dual Monitor Installation</li>
          <li>Mounting Hardware</li><li>Wireless Installation</li><li>Office Sound Solutions</li>
          <li>Custom Dental Cable</li><li>Video Surveillance</li>
        </ul>
      </div>
    </div>

    <div class="abs solutions">
      <h2 class="section-title"><b>SOLUTIONS</b></h2><span class="rule"></span>
      <ul class="ticks">
        <li>Flat Rate Monthly Support</li>
        <li>Secure Backups with our ChairsideVault.com</li>
        <li>Secure Encrypted Emails &amp; X-Rays</li>
        <li>Practice Management Software Experts</li>
        <li>HIPAA Compliance</li>
        <li>Anti-Virus, Anti-Malware and Cyber Security</li>
        <li>Data Recovery</li>
        <li>Cloud Email &amp; Office Suites</li>
        <li>Phone VOIP &amp; SIP Trunks</li>
      </ul>
    </div>

    <div class="abs ready">
      <h2>READY TO MAKE<br>YOUR TECHNOLOGY<br>WORK?</h2><span class="rule"></span>
      <h3>How To Achieve Technology Bliss for Your Practice</h3>
      <ul class="ticks">
        <li>Schedule a FREE Network &amp; Technology Evaluation</li>
        <li>Receive your Flat Rate Price and Technology Quote</li>
        <li>Sit back and let Byte Harbor take care of everything.</li>
      </ul>
      <p>Don't let Technology Departments, Hardware Vendors and Practice Management vendors Point Fingers at each other.</p>
      <p>We collaborate everything and everyone for you, make one call to us and let us handle your technology.</p>
    </div>
  </section>

</main>
</body>
</html>
```